Ten-Harvest Brochure

We would like a 3 panel layout format with copy on both sides and on each panel, (we will provide content).

We are Ten-Harvest and we work with business owners to achieve measurable growth and success based on 5 Core Pillars Of Momentum and (S.L.K) 60 Week Progress Roadmap Scheme. We also work with the business leader and individuals within the organization with personal development.

We would like the brochure to have a corporate feel, but warm and inviting. We don't want a hard or aggressive feel.

We would like it to be available for pdf upload and physical print formats.

The winning design will also be invited to design a header for our website as well. The header will be consistent with the brochure, so please keep that in mind during your creative process.

I am enclosing a transparent copy of our company logo along with content for the brochure.

Thank you in advance for your consideration!

Gareth and Moira
Updates

Sorry, but we forgot to include the front cover text.

It will read as follows,

Do you know the 5 Core Pillars Of Momentum  that are crucial to the success of any business today?

Also, please add the following to the back page

Website: www.ten-harvest.example
Resource Centre: www.thresourcehub.example 
Phone: +44 (0) 7612583047
Email: info@ten-harvest.example

Follow us on (please insert Facebook, Linkedin and YouTube logo)

I have uploaded a pdf format of brochure text.

Hello designers. I wanted to give some further input to help the process. Although the brochure is to target business, we don't want to over do it with corporate professioanls in all the photos. If there is an opportunity to incorporate photos of small business owners like, a butcher, baker, chef, flower shop etc. This would hopefully help us make an immpression to all small business owners.

Thank you, and good luck!

Gareth and Moira  

Reason: A few designers have come come on board last minute. So I'd like to give everyone the same opportunity to respond. Sincerely, Gareth

Target Market(s)

Small Business Owners searching for new ways to grow their business in the UK and Republic Of Ireland.

Industry/Entity Type

Business

```html
<!DOCTYPE html>
<html lang="en">
<head>
<meta charset="utf-8">
<title>Ten-Harvest Brochure</title>
<link href="https://fonts.googleapis.com/css2?family=Open+Sans:wght@400&family=Roboto+Condensed:wght@400;700;800&display=swap" rel="stylesheet">
<style>
  :root {
    --purple: #6a2570;
    --purple-light: #9a4fa0;
    --grey: #6b6b6b;
    --grey-dark: #4a4a4a;
    --band-grey: #8a8a8a;
    --cream: #f7f0c0;
    --paper: #ffffff;
    --backdrop: #e9e6e2;
    --text: #3c3c3c;
  }
  * { box-sizing: border-box; margin: 0; padding: 0; }
  html, body { width: 1200px; height: 960px; overflow: hidden; }
  body { background: var(--backdrop); font-family: "Open Sans", sans-serif; }

  .brochure {
    position: absolute; left: 30px; top: 30px;
    width: 1140px; height: 900px;
    background: var(--paper);
    box-shadow: 0 6px 24px rgba(0,0,0,.18);
    overflow: hidden;
  }
  .panel { position: absolute; top: 0; width: 380px; height: 900px; }
  .panel--inside { left: 0; }
  .panel--back { left: 380px; border-left: 1px solid #eee; }
  .panel--cover { left: 760px; border-left: 1px solid #eee; }

  .hero { position: absolute; left: 380px; top: 0; width: 760px; height: 540px; }

  .section-title {
    position: absolute; left: 40px; top: 110px;
    font-family: "Roboto Condensed", sans-serif; font-weight: 700;
    font-size: 26px; color: var(--purple);
  }
  .intro {
    position: absolute; left: 40px; top: 190px; width: 310px;
    font-size: 13.5px; line-height: 1.55; color: var(--text);
  }
  .savings-photo {
    position: absolute; left: 110px; top: 500px; width: 150px; height: 290px;
    border-radius: 20px 20px 26px 26px;
    background: linear-gradient(180deg, #3f7a2c 0%, #5e9a3c 30%, #9a7a55 45%, #7a5a3c 100%);
  }

  .band { position: absolute; left: 0; top: 850px; width: 760px; }
  .band__purple { height: 14px; background: var(--purple); }
  .band__grey { height: 10px; background: var(--band-grey); }

  .brand {
    position: absolute; display: flex; align-items: center; gap: 10px;
    font-family: "Roboto Condensed", sans-serif; font-weight: 700;
    font-size: 26px; letter-spacing: 3px; text-transform: uppercase; color: var(--purple);
  }
  .brand__mark { width: 22px; height: 22px; background: var(--grey); }
  .panel--back .brand { left: 0; right: 0; justify-content: center; top: 565px; }
  .panel--cover .brand { left: 40px; top: 575px; }

  .contacts {
    position: absolute; left: 0; right: 0; top: 640px;
    text-align: center; font-family: "Roboto Condensed", sans-serif; font-style: normal;
    font-size: 18px; line-height: 28px; color: var(--grey-dark);
  }
  .social { position: absolute; left: 0; right: 0; top: 772px; display: flex; justify-content: center; gap: 12px; }
  .social__item { width: 30px; height: 30px; border-radius: 4px; background: var(--purple); }

  .cover-lead {
    position: absolute; left: 40px; top: 650px;
    font-family: "Roboto Condensed", sans-serif; font-size: 28px; line-height: 1.2; color: var(--purple-light);
  }
  .cover-title {
    position: absolute; left: 40px; top: 694px; width: 330px;
    font-family: "Roboto Condensed", sans-serif; font-weight: 800;
    font-size: 46px; line-height: 1; text-transform: uppercase; color: var(--purple);
  }
  .cover-sub {
    position: absolute; right: 24px; top: 800px; width: 320px; text-align: right;
    font-family: "Roboto Condensed", sans-serif; font-weight: 700;
    font-size: 19px; line-height: 1.25; color: var(--grey);
  }
</style>
</head>
<body>
<main class="brochure">
  <section class="panel panel--inside">
    <h2 class="section-title">The New Economy</h2>
    <p class="intro">The economy is finally beginning to show signs of recovery. You may not realize that small to medium businesses generate half of the U.K's national income and two thirds of all employment, so undoubtedly they are playing a major role in this “new economy” that is emerging. Business is changing fast and it is more competitive than ever, so it is vital to the success of any company, to find innovative and creative ways to attract new customers, keep them coming back and stay ahead of the competition.</p>
    <div class="savings-photo" role="img" aria-label="Young green plant growing from a glass jar filled with coins"></div>
  </section>

  <svg class="hero" viewBox="0 0 760 540" role="img" aria-label="Smiling florist holding a flower arrangement in a sunny flower shop">
    <defs>
      <linearGradient id="heroTones" x1="0" y1="0" x2="1" y2="1">
        <stop offset="0" stop-color="#d9a13a"/>
        <stop offset="0.45" stop-color="#e8b75a"/>
        <stop offset="0.7" stop-color="#8a9a4e"/>
        <stop offset="1" stop-color="#5c7a3a"/>
      </linearGradient>
    </defs>
    <path d="M0,0 H760 V540 Q420,470 0,460 Z" fill="var(--cream)"/>
    <path d="M16,0 H760 V510 Q420,448 16,440 Z" fill="url(#heroTones)"/>
  </svg>

  <section class="panel panel--back">
    <div class="brand"><span class="brand__mark"></span>Ten-Harvest</div>
    <address class="contacts">
      Website: www.ten-harvest.example<br>
      Resource Centre: www.thresourcehub.example<br>
      Phone: +44 (0) 7612583047<br>
      Email: info@ten-harvest.example
    </address>
    <div class="social" aria-label="Social channels">
      <span class="social__item"></span>
      <span class="social__item"></span>
      <span class="social__item"></span>
    </div>
  </section>

  <section class="panel panel--cover">
    <div class="brand"><span class="brand__mark"></span>Ten-Harvest</div>
    <p class="cover-lead">Do you know the</p>
    <h1 class="cover-title">5 Core Pillars of Momentum</h1>
    <p class="cover-sub">that are crucial to the success of any business today?</p>
  </section>

  <div class="band"><div class="band__purple"></div><div class="band__grey"></div></div>
</main>
</body>
</html>
```